World Wide News and Current Affairs website

We intends to start up a new website which deals on New and Current Affairs.
Attention Designers,
We want a home page design for this project. Our business is based in the United States. Our goal is to become a well known brand.
The website would consist of a category for News, Business and Tech.
The theme should be beautiful and attention seeking. The website would take bulk of it's news from the US, and Europe.
Designers can get inspiration from already existing new websites such as PWJ, KLV, DASKOLM.
All designs should be clean and easy to navigate.

```html
<!DOCTYPE html>
<html lang="en">
<head>
<meta charset="utf-8">
<title>Global News — Home</title>
<link rel="stylesheet" href="https://fonts.googleapis.com/css2?family=Oswald:wght@300;400;500;600&family=Open+Sans:wght@400;600;700&display=swap">
<style>
:root{
  --red:#d9161c;
  --red-dark:#b50f14;
  --ink:#222;
  --text:#555;
  --muted:#8a8a8a;
  --line:#e2e2e2;
  --panel:#f3f3f3;
  --dark:#1c1c1c;
  --darker:#141414;
  --blue:#1c9ad6;
  --white:#fff;
  --head:'Oswald',sans-serif;
  --body:'Open Sans',sans-serif;
}
*{box-sizing:border-box;margin:0;padding:0}
html,body{width:1200px;height:4651px;overflow:hidden}
body{font-family:var(--body);color:var(--text);background:var(--white);font-size:12px;position:relative}
.wrap{width:740px;margin:0 auto;position:relative}
.ph{display:block}

/* ---------- hero ---------- */
.hero{position:relative;height:543px;background:linear-gradient(180deg,#3a4f63 0%,#7d7f80 30%,#d49a5c 48%,#8c7a68 62%,#5b5a5a 100%);overflow:hidden}
.topbar{position:absolute;top:0;left:0;right:0;height:72px;background:rgba(20,20,20,.55)}
.topbar .wrap{height:72px;display:flex;align-items:center}
.logo{background:var(--red);color:#fff;font-family:var(--head);font-weight:600;font-size:30px;height:72px;width:108px;display:flex;align-items:center;justify-content:center;letter-spacing:1px}
.topbar .quick{position:absolute;top:6px;left:150px;right:0;display:flex;justify-content:space-between;font-size:8px;color:#ccc}
.nav{display:flex;margin-left:14px;margin-top:26px}
.nav a{color:#ddd;font-size:10px;text-decoration:none;padding:6px 10px;text-transform:uppercase}
.nav a.on{background:#fff;color:var(--ink);font-weight:700}
.cta{margin-left:auto;margin-top:26px;background:var(--blue);color:#fff;font-size:9px;font-weight:700;padding:6px 12px}
.hero-copy{position:absolute;left:233px;top:182px;color:#fff}
.hero-copy .stamp{display:inline-block;background:var(--red);font-family:var(--head);font-size:13px;padding:2px 8px;letter-spacing:1px}
.hero-copy .date{font-family:var(--head);font-size:13px;margin-left:6px}
.hero-copy h1{font-family:var(--head);font-weight:400;font-size:104px;line-height:1.05;letter-spacing:2px;margin-top:4px;white-space:nowrap}
.hero-copy p{font-family:var(--head);font-size:20px;letter-spacing:1px;margin-top:-6px}
.hero-side{position:absolute;left:820px;top:236px;color:#fff;font-family:var(--head);font-size:10px;line-height:1.25;width:110px;opacity:.9;display:flex;gap:8px;align-items:flex-start}
.hero-side svg{flex:none}
.featured{position:absolute;left:233px;right:233px;top:434px;height:100px;background:rgba(10,10,10,.75);display:flex;align-items:center;padding:0 10px}
.featured .label{font-family:var(--head);color:#fff;font-size:18px;line-height:1.05;width:120px}
.featured .label b{color:var(--red);font-weight:500;display:block}
.feat-item{display:flex;gap:8px;width:150px;margin-left:6px}
.feat-item .ph{width:62px;height:70px;background:linear-gradient(160deg,#6f8a5d,#3d5a3a)}
.feat-item span{color:#eee;font-size:9px;line-height:1.35}
.breaking{height:25px;background:var(--red);color:#fff;font-size:10px}
.breaking .wrap{display:flex;align-items:center;height:25px;gap:16px;white-space:nowrap;overflow:hidden}
.breaking b{font-family:var(--head);font-weight:500;font-size:12px;letter-spacing:.5px}
.tabs{height:57px;border-bottom:1px solid var(--line)}
.tabs .wrap{display:flex;padding-top:12px}
.tabs a{flex:1;text-align:center;font-size:9px;font-weight:600;color:#777;padding:12px 0;border:1px solid var(--line);border-left:none;background:#fafafa;text-decoration:none}
.tabs a:first-child{border-left:1px solid var(--line);background:#fff;color:var(--ink)}

/* ---------- section heading ---------- */
.sec-head{display:flex;align-items:flex-start;gap:10px}
.sec-head:before{content:"";width:5px;height:52px;background:var(--red)}
.sec-head h2{font-family:var(--head);font-weight:500;font-size:34px;color:var(--ink);line-height:1}
.sec-head small{display:block;font-family:var(--head);font-size:12px;color:#777;letter-spacing:1px;margin-top:2px}

/* ---------- hot news ---------- */
.hot{height:635px;padding-top:50px}
.view-toggle{position:absolute;right:0;top:16px;display:flex;gap:4px}
.view-toggle i{width:12px;height:12px;background:#444;display:block}
.view-toggle i+i{background:#bbb}
.hot-grid{display:flex;gap:15px;margin-top:62px}
.lead{width:435px;height:189px;display:flex}
.lead .ph{width:270px;background:linear-gradient(135deg,#b79a86,#6e5348)}
.lead .copy{flex:1;background:var(--red);color:#fff;padding:18px 14px}
.lead h3{font-family:var(--head);font-weight:400;font-size:20px;line-height:1.1}
.lead p{font-size:8px;margin-top:10px;line-height:1.5}
.lead .more{display:inline-block;background:#fff;color:var(--red);font-size:8px;font-weight:700;padding:4px 10px;margin-top:10px}
.side-list{flex:1;display:grid;grid-template-columns:1fr 1fr;gap:12px 12px}
.mini{display:flex;gap:8px}
.mini .ph{width:44px;height:44px;flex:none;background:linear-gradient(135deg,#8fa0b0,#4e5e6e)}
.mini h4{font-family:var(--head);font-weight:400;color:var(--red);font-size:10px;line-height:1.15}
.mini p{font-size:7px;line-height:1.4;margin-top:2px}
.thumbs{display:flex;gap:10px;margin-top:46px}
.thumb{flex:1}
.thumb .ph{height:110px;background:linear-gradient(135deg,#a7b2bd,#556270);position:relative}
.thumb .ph:after{content:"";position:absolute;left:0;bottom:0;width:30px;height:8px;background:var(--blue)}
.thumb p{font-family:var(--head);font-size:10px;color:var(--ink);margin-top:6px;line-height:1.2}
.thumb .tag{display:inline-block;background:#333;color:#fff;font-size:7px;padding:1px 4px;margin-left:4px}

/* ---------- videos ---------- */
.videos-head{height:140px;padding-top:27px}
.videos{height:370px;background:var(--dark);display:flex}
.videos .ph{width:744px;position:relative;background:linear-gradient(90deg,#3b3b3b,#8a8a8a 45%,#2b2b2b 85%)}
.videos .over{position:absolute;left:380px;top:120px;color:#fff}
.videos .over small{font-family:var(--head);font-size:14px}
.videos .over h3{font-family:var(--head);font-weight:400;font-size:34px;line-height:1.1}
.videos .over .play{display:inline-flex;align-items:center;gap:8px;margin-top:22px;background:var(--red);font-size:10px;font-weight:700;padding:8px 14px}
.vlist{width:225px;padding:10px 0 0 0}
.vitem{display:flex;gap:10px;justify-content:flex-end;margin-bottom:12px}
.vitem p{font-family:var(--head);font-size:10px;color:var(--red);width:60px;line-height:1.2;text-align:right}
.vitem p span{display:block;color:#aaa;font-family:var(--body);font-size:7px}
.vitem .ph{width:110px;height:74px;background:linear-gradient(135deg,#8a6a54,#3c2c24)}

/* ---------- prime news ---------- */
.prime{height:660px;padding-top:85px}
.about{display:flex;gap:40px;margin-top:60px}
.about .txt{width:440px}
.about h3,.partners h3{font-family:var(--head);font-weight:400;font-size:14px;color:var(--ink);margin-bottom:14px}
.about .txt p{font-size:9px;line-height:1.55;margin-bottom:12px}
.desk{flex:1;border:1px solid var(--line);padding:14px;height:200px}
.desk h4{font-family:var(--head);font-weight:300;font-size:20px;color:var(--ink);display:flex;align-items:center;gap:10px;border-bottom:1px solid var(--line);padding-bottom:10px;margin-bottom:10px}
.desk h4 i{width:26px;height:26px;border:1px solid #999;border-radius:50%;display:block}
.desk p{font-size:8px;line-height:1.55;margin-bottom:8px}
.partners{margin-top:14px}
.badges{display:flex;gap:16px}
.badges div{width:130px;height:80px;border:1px solid var(--line);display:flex;align-items:center;justify-content:center}
.badges span{width:48px;height:48px;border-radius:50%;background:#333}

/* ---------- widgets ---------- */
.widgets-head{height:140px;padding-top:35px}
.widgets{height:910px;background:var(--panel);padding-top:20px}
.wcols{display:grid;grid-template-columns:145px 185px 200px 180px;gap:10px}
.card{background:#fff;border:1px solid var(--line);margin-bottom:10px}
.card .hd{font-size:8px;font-weight:700;padding:8px 10px;color:var(--ink)}
.card .bd{padding:8px 10px;font-size:7.5px;line-height:1.5}
.redhd{background:var(--red);color:#fff!important}
.bluehd{background:var(--blue);color:#fff!important}
.twotab{display:flex}
.twotab span{flex:1;padding:8px 10px;font-size:8px;font-weight:700}
.list li{list-style:none;padding:6px 0 6px 12px;border-bottom:1px solid #eee;position:relative;font-size:7.5px}
.list li:before{content:"";position:absolute;left:0;top:9px;width:5px;height:5px;background:var(--red);border-radius:50%}
.wrow{display:flex;gap:8px;padding:7px 10px;border-bottom:1px solid #eee}
.wrow .ph{width:40px;height:30px;flex:none;background:linear-gradient(135deg,#c28e5c,#7c5234)}
.wrow p{font-size:7.5px;line-height:1.35}
.wrow p b{color:var(--red);font-weight:600}
.tweet{display:flex;gap:8px;padding:9px 10px;border-bottom:1px solid #eee;font-size:7.5px;line-height:1.4}
.tweet i{width:26px;height:26px;flex:none;background:#9aa9b6}
.tweet b{color:var(--blue)}
.poll{background:var(--red);color:#fff;padding:14px 12px;height:235px}
.poll small{font-size:8px;font-weight:700}
.poll h4{font-family:var(--head);font-weight:400;font-size:17px;line-height:1.15;margin:16px 0 14px}
.poll .opt{display:flex;align-items:center;gap:6px;font-size:8px;margin-bottom:7px}
.poll .opt i{width:9px;height:9px;border:1px solid #fff;border-radius:50%}
.poll .sub{display:inline-block;background:#fff;color:var(--red);font-size:8px;font-weight:700;padding:5px 12px;margin-top:8px;margin-left:70px}
.weather{background:var(--blue);color:#fff;height:250px;padding:12px}
.weather small{font-size:8px;font-weight:700}
.weather .city{font-size:9px;margin-top:24px}
.weather .deg{font-family:var(--head);font-weight:300;font-size:70px;line-height:1}
.weather .sun{position:absolute;right:18px;top:70px}
.weather .row{display:flex;justify-content:space-between;font-size:7px;border-top:1px solid rgba(255,255,255,.4);margin-top:22px;padding-top:8px}
.soc{display:flex;align-items:center;gap:8px;padding:6px 10px;font-size:7.5px;border-bottom:1px solid #eee}
.soc i{width:18px;height:18px;display:block}
.soc .btn{margin-left:auto;border:1px solid #ccc;padding:2px 6px;font-size:7px}
.news-row{display:flex;gap:8px;align-items:center;padding:6px 10px;border-bottom:1px solid #eee;font-size:7.5px}
.news-row i{width:14px;height:14px;border:1px solid #bbb;border-radius:50%;flex:none}
.grid9{display:grid;grid-template-columns:repeat(3,1fr);gap:3px;padding:8px}
.grid9 span{height:50px;background:linear-gradient(135deg,#b4875e,#5d4a3c)}
.grid9 span:nth-child(even){background:linear-gradient(135deg,#a26a4a,#3f5b35)}
.pv{background:var(--dark);color:#fff;margin-bottom:10px}
.pv .twotab span{color:#fff}
.pv .twotab span+span{background:var(--red)}
.pv .wrow{border-color:#333}
.pv .wrow p{color:#bbb}
.pv .wrow p b{color:#f24b50}
.stock{display:flex;align-items:center;justify-content:space-between;padding:7px 10px;font-size:7.5px;border-bottom:1px solid #eee}
.stock span{color:#fff;font-size:7px;padding:3px 6px;width:78px}

/* ---------- correspondents ---------- */
.corr{height:510px;padding-top:48px}
.people{display:flex;gap:10px;margin-top:55px}
.person{flex:1}
.person .ph{height:130px;background:linear-gradient(180deg,#d4cfca,#8b7f76)}
.person .name{background:var(--red);color:#fff;padding:8px 8px;height:54px;position:relative}
.person .name b{font-family:var(--head);font-weight:500;font-size:11px;display:block}
.person .name span{font-size:7px}
.person .name i{position:absolute;right:8px;top:-10px;width:20px;height:20px;border-radius:50%;background:var(--ink);border:2px solid #fff}
.corr h5{font-family:var(--head);font-weight:400;font-size:11px;color:var(--ink);margin-top:26px}
.corr .note{font-size:8px;line-height:1.55;margin-top:6px}

/* ---------- contact ---------- */
.contact{height:320px;display:flex}
.map{width:667px;position:relative;background:linear-gradient(135deg,#e6e6e6,#cfcfcf 55%,#e2e2e2)}
.pin{position:absolute;left:410px;top:100px;background:var(--red);color:#fff;font-family:var(--head);font-size:12px;padding:12px 16px;display:flex;align-items:center;gap:8px}
.pin:after{content:"";position:absolute;left:20px;bottom:-10px;border:10px solid transparent;border-top-color:var(--red);border-bottom:0}
.hq{flex:1;background:#2a2a2a;color:#bbb;padding:22px 40px;font-size:8px;line-height:1.6}
.hq h4{font-family:var(--head);font-weight:400;color:#fff;font-size:13px;margin-bottom:8px}
.hq .ln{display:flex;align-items:center;gap:10px;margin-top:10px}
.hq .ln i{width:16px;height:16px;border-radius:50%;background:#444;display:block}
.hq .social{display:flex;gap:6px;margin:6px 0 22px}
.hq .social i{width:18px;height:18px;border-radius:50%;background:#555}
.hq h6{color:var(--blue);font-size:9px;margin-top:14px}
.sub-form{display:flex}
.sub-form span{flex:1;background:#3a3a3a;color:#888;padding:8px 10px}
.sub-form b{background:var(--red);color:#fff;padding:8px 14px}

/* ---------- footer ---------- */
.footer{height:341px;background:var(--darker);padding-top:30px}
.footer .wrap{display:flex;gap:20px}
.fcol{width:95px}
.fcol h6{color:#fff;font-size:8px;margin-bottom:6px}
.fcol a{display:block;color:#888;font-size:7.5px;line-height:1.85;text-decoration:none}
.fbrand{margin-left:auto;width:170px;padding-top:40px}
.fbrand .logo{height:60px;width:120px;font-size:24px;background:transparent;border:1px solid #333;color:var(--red)}
.fbrand p{color:#666;font-size:7px;line-height:1.5;margin-top:70px}
</style>
</head>
<body>

<header class="hero">
  <div class="ph" role="img" aria-label="City skyline at sunset seen from above" style="position:absolute;inset:0"></div>
  <div class="topbar">
    <div class="wrap">
      <div class="quick"><span>Live Broadcast Channel</span><span>Select Country &nbsp;▾ &nbsp;&nbsp; Sign in &nbsp;|&nbsp; Register</span></div>
      <div class="logo">LOGO</div>
      <nav class="nav">
        <a class="on" href="#">Home</a><a href="#">About us</a><a href="#">Services</a><a href="#">Videos</a><a href="#">News</a><a href="#">Contact us</a>
      </nav>
      <div class="cta">BECOME A CORRESPONDENT</div>
    </div>
  </div>
  <div class="hero-copy">
    <span class="stamp">THE NEW 14:55:12</span><span class="date">WEDNESDAY, MAY 14, 2014</span>
    <h1>GLOBAL NEWS</h1>
    <p>AT YOUR FINGER TIPS</p>
  </div>
  <div class="hero-side">
    <svg width="14" height="22" viewBox="0 0 14 22"><rect x="1" y="1" width="12" height="20" rx="2" fill="none" stroke="#fff" stroke-width="1.5"/><circle cx="7" cy="17.5" r="1.2" fill="#fff"/></svg>
    <span>DOWNLOAD<br>THE NEWS APP<br>ON YOUR PHONE</span>
  </div>
  <div class="featured">
    <div class="label">FEATURED<b>NEWS</b></div>
    <div class="feat-item"><div class="ph" role="img" aria-label="Match photo"></div><span>Champions take the final after a late winner</span></div>
    <div class="feat-item"><div class="ph" role="img" aria-label="Player on the field"></div><span>Star forward signs a record new contract</span></div>
    <div class="feat-item"><div class="ph" role="img" aria-label="Stadium crowd"></div><span>Fans fill the stadium for season opener</span></div>
    <div class="feat-item"><div class="ph" role="img" aria-label="Coach on sideline"></div><span>Coach names squad for the summer tour</span></div>
  </div>
</header>

<div class="breaking"><div class="wrap"><b>BREAKING NEWS</b><span>Markets rally after leaders agree on new trade plan — talks resume next week in Geneva</span></div></div>

<div class="tabs"><div class="wrap">
  <a href="#">POLITICS</a><a href="#">SPORTS</a><a href="#">ENTERTAINMENT</a><a href="#">BUSINESS</a><a href="#">EDUCATION</a><a href="#">SCIENCE</a><a href="#">WORLD</a><a href="#">SOCIAL</a><a href="#">LIFESTYLE</a><a href="#">AUTOMOTIVE</a>
</div></div>

<section class="hot"><div class="wrap">
  <div class="sec-head"><div><h2>HOT NEWS</h2><small>AROUND THE WORLD</small></div></div>
  <div class="view-toggle"><i></i><i></i></div>
  <div class="hot-grid">
    <article class="lead">
      <div class="ph" role="img" aria-label="Politicians at a debate"></div>
      <div class="copy"><h3>THE BIG<br>POLITICAL DEBATE</h3><p>Candidates clash over taxes, health care and jobs in a heated night on the main stage.</p><span class="more">READ MORE</span></div>
    </article>
    <div class="side-list">
      <div class="mini"><div class="ph" role="img" aria-label="News photo"></div><div><h4>NEW BUDGET WILL BE PASSED</h4><p>Lawmakers reach a deal late on Friday night in the capital.</p></div></div>
      <div class="mini"><div class="ph" role="img" aria-label="News photo"></div><div><h4>NEW RAIL LINE WILL OPEN</h4><p>The route links two cities in under an hour from next spring.</p></div></div>
      <div class="mini"><div class="ph" role="img" aria-label="News photo"></div><div><h4>NEW TALKS WILL BEGIN</h4><p>Envoys meet again to settle the long border dispute.</p></div></div>
      <div class="mini"><div class="ph" role="img" aria-label="News photo"></div><div><h4>NEW LAWS WILL BE VOTED</h4><p>The house will debate the reform bill early next week.</p></div></div>
    </div>
  </div>
  <div class="thumbs">
    <div class="thumb"><div class="ph" role="img" aria-label="Portrait news photo"></div><p>ON THE CAMPAIGN TRAIL WITH VOTERS <span class="tag">POLITICS</span></p></div>
    <div class="thumb"><div class="ph" role="img" aria-label="Business meeting photo"></div><p>BANKS CUT RATES FOR NEW BUYERS <span class="tag">BUSINESS</span></p></div>
    <div class="thumb"><div class="ph" role="img" aria-label="Group photo"></div><p>STUDENTS WIN THE SCIENCE PRIZE <span class="tag">SCIENCE</span></p></div>
    <div class="thumb"><div class="ph" role="img" aria-label="Food photo"></div><p>CHEFS SHARE THEIR SUMMER DISHES <span class="tag">LIFESTYLE</span></p></div>
    <div class="thumb"><div class="ph" role="img" aria-label="Football player photo"></div><p>ROOKIE LEADS TEAM TO BIG WIN <span class="tag">SPORTS</span></p></div>
  </div>
</div></section>

<div class="videos-head"><div class="wrap"><div class="sec-head"><div><h2>RECENT VIDEOS</h2><small>AROUND THE WORLD</small></div></div></div></div>
<section class="videos">
  <div class="ph" role="img" aria-label="Black and white portrait of an elderly man">
    <div class="over">
      <small>VIDEO OF THE DAY</small>
      <h3>TITLE OF THE VIDEO</h3>
      <span class="play">PLAY VIDEO
        <svg width="12" height="12" viewBox="0 0 12 12"><circle cx="6" cy="6" r="5.5" fill="none" stroke="#fff"/><path d="M5 3.5 8 6 5 8.5z" fill="#fff"/></svg></span>
    </div>
  </div>
  <div class="vlist">
    <div class="vitem"><p>NEW STORY ON THE CITY<span>2 min ago</span></p><div class="ph" role="img" aria-label="Video still"></div></div>
    <div class="vitem"><p>NEW INTERVIEW RELEASED<span>8 min ago</span></p><div class="ph" role="img" aria-label="Video still"></div></div>
    <div class="vitem"><p>NEW REPORT FROM ABROAD<span>1 hour ago</span></p><div class="ph" role="img" aria-label="Video still"></div></div>
    <div class="vitem"><p>NEW CONCERT FOOTAGE<span>3 hours ago</span></p><div class="ph" role="img" aria-label="Video still"></div></div>
  </div>
</section>

<section class="prime"><div class="wrap">
  <div class="sec-head"><div><h2>PRIME NEWS</h2><small>KNOW MORE ABOUT US</small></div></div>
  <div class="about">
    <div class="txt">
      <h3>ABOUT US</h3>
      <p>We are an independent newsroom covering politics, business and technology across the United States and Europe. Our reporters work around the clock to bring you the stories that shape the day, checked and explained in plain words.</p>
      <p>From city halls to trading floors, our teams follow events as they unfold. We aim to give readers the facts first, then the context that helps them understand why it matters and what comes next for them.</p>
      <p>Our network of correspondents spans more than forty countries. Every story is reviewed by an editor before it goes live, and every correction is marked clearly so you always know what changed.</p>
    </div>
    <aside class="desk">
      <h4><i></i>Editor's desk</h4>
      <p>Each morning our editors choose the stories that matter most and explain why. Read their picks, notes and thoughts on the news behind the headlines.</p>
      <p>This week the desk looks at the trade talks, the new tech rules in Europe and the race for the state house seats.</p>
    </aside>
  </div>
  <div class="partners">
    <h3>OUR GLOBAL NEWS PARTNERS</h3>
    <div class="badges"><div><span></span></div><div><span></span></div><div><span></span></div><div><span></span></div><div><span></span></div></div>
  </div>
</div></section>

<div class="widgets-head"><div class="wrap"><div class="sec-head"><div><h2>GREAT WIDGETS</h2><small>SOME GREAT FEATURES</small></div></div></div></div>
<section class="widgets"><div class="wrap wcols">
  <div>
    <div class="card"><div class="hd">✎ EDITOR'S PIC</div><div class="bd">Our editor picks the one story you should not miss today, with a short note on why it stands out from the rest of the news and what to watch for next.<br><br>Read the full piece and share your view with the team.</div></div>
    <div class="card"><div class="hd">☰ THE LIST</div><div class="bd"><ul class="list">
      <li>Ten cities with the best new parks</li><li>Five ways to cut your bills</li><li>The week's top tech launches</li><li>Seven books for the summer</li><li>Best trains across Europe</li><li>New laws in force this month</li><li>The year's top small firms</li><li>Films to watch this weekend</li><li>Where rents rose the most</li><li>Quiet towns worth a visit</li><li>Top apps for saving money</li><li>Markets to watch next week</li><li>Stars who made the news</li><li>Startups changing travel</li><li>Ideas for a greener home</li>
    </ul></div></div>
  </div>
  <div>
    <div class="card"><div class="twotab"><span class="redhd">MOST POPULAR</span><span>RECENT</span></div>
      <div class="wrow"><div class="ph" role="img" aria-label="News photo"></div><p><b>NEW MARKET HIGH</b><br>Stocks close the week up</p></div>
      <div class="wrow"><div class="ph" role="img" aria-label="News photo"></div><p><b>NEW PHONE REVEALED</b><br>First look at the device</p></div>
      <div class="wrow"><div class="ph" role="img" aria-label="News photo"></div><p><b>NEW SEASON STARTS</b><br>Teams ready for kick off</p></div>
    </div>
    <div class="card"><div class="hd bluehd">FOLLOW US ON CHIRPLINE</div>
      <div class="tweet"><i></i><p><b>@hq_newsroom</b> Leaders meet today to sign the new trade deal. Live updates on our site.</p></div>
      <div class="tweet"><i></i><p><b>@hq_newsroom</b> Storm warning issued for the east coast this weekend.</p></div>
      <div class="tweet"><i></i><p><b>@hq_newsroom</b> Watch the full debate again on our video page tonight.</p></div>
    </div>
    <div class="poll"><small>CONTACT SECTION</small>
      <h4>YOUR POLL QUESTIONS WILL APPEAR HERE WITH SHORT DESCRIPTION, DO YOU WANT TO SAY THIS?</h4>
      <div class="opt"><i></i>Yes, I agree</div><div class="opt"><i></i>No, not at all</div><div class="opt"><i></i>Not sure yet</div>
      <span class="sub">SUBMIT</span>
    </div>
  </div>
  <div>
    <div class="card weather" style="position:relative;border:none">
      <small>WEATHER</small>
      <div class="city">NEW YORK, NY · 2PM</div>
      <div class="deg">32°c</div>
      <svg class="sun" width="48" height="48" viewBox="0 0 48 48"><circle cx="24" cy="24" r="10" fill="#fff"/><g stroke="#fff" stroke-width="3"><path d="M24 2v7M24 39v7M2 24h7M39 24h7M8 8l5 5M35 35l5 5M40 8l-5 5M13 35l-5 5"/></g></svg>
      <div class="row"><span>MON 30°</span><span>TUE 28°</span><span>WED 31°</span><span>THU 27°</span></div>
    </div>
    <div class="card"><div class="hd">SOCIAL WITH US</div>
      <div class="soc"><i style="background:#4a5f7a"></i>Like our page<span class="btn">Like</span></div>
      <div class="soc"><i style="background:var(--blue)"></i>Follow our news<span class="btn">Follow</span></div>
      <div class="soc"><i style="background:var(--red)"></i>Join our group<span class="btn">Join</span></div>
      <div class="soc"><i style="background:#b5487a"></i>See our photos<span class="btn">View</span></div>
      <div class="soc"><i style="background:#f39c12"></i>Read our feed<span class="btn">Subscribe</span></div>
    </div>
    <div class="card"><div class="twotab"><span>POPULAR NEWS</span><span class="bluehd">RECENT NEWS</span></div>
      <div class="news-row"><i></i>City council backs new bike lanes</div>
      <div class="news-row"><i></i>Airline adds direct route to Lisbon</div>
      <div class="news-row"><i></i>Tech firm hires five hundred staff</div>
      <div class="news-row"><i></i>Museum opens its new modern wing</div>
      <div class="news-row"><i></i>Farmers hope for rain next week</div>
      <div class="news-row"><i></i>School year to start a week early</div>
    </div>
  </div>
  <div>
    <div class="card"><div class="hd">WHAT'S UP LIVE</div>
      <div class="grid9" role="img" aria-label="Grid of live photo thumbnails"><span></span><span></span><span></span><span></span><span></span><span></span><span></span><span></span><span></span></div>
    </div>
    <div class="pv"><div class="twotab"><span>POPULAR VIDEOS</span><span>RECENT VIDEOS</span></div>
      <div class="wrow"><div class="ph" role="img" aria-label="Video still"></div><p><b>NEW STREET FESTIVAL</b><br>Crowds fill downtown</p></div>
      <div class="wrow"><div class="ph" role="img" aria-label="Video still"></div><p><b>NEW ROCKET TEST</b><br>Launch goes to plan</p></div>
      <div class="wrow"><div class="ph" role="img" aria-label="Video still"></div><p><b>NEW BRIDGE OPENS</b><br>Traffic flows at last</p></div>
    </div>
    <div class="card"><div class="twotab"><span class="redhd">STOCKS</span><span>INDEX</span><span>RATES</span></div>
      <div class="stock">INDEX ONE<span style="background:#2fa24a">▲ 1.24% 16,512</span></div>
      <div class="stock">INDEX TWO<span style="background:var(--red)">▼ 0.38% 4,102</span></div>
      <div class="stock">INDEX THREE<span style="background:#f0a020">■ 0.00% 1,877</span></div>
      <div class="stock">INDEX FOUR<span style="background:#2fa24a">▲ 0.91% 6,840</span></div>
    </div>
  </div>
</div></section>

<section class="corr"><div class="wrap">
  <div class="sec-head"><div><h2>GLOBAL CORRESPONDENTS</h2><small>MEET OUR WORLDWIDE MEMBERS</small></div></div>
  <div class="people">
    <div class="person"><div class="ph" role="img" aria-label="Portrait of a correspondent"></div><div class="name"><i></i><b>JORAN VELD</b><span>Washington Desk</span></div></div>
    <div class="person"><div class="ph" role="img" aria-label="Portrait of a correspondent"></div><div class="name"><i></i><b>MIRA SOLT</b><span>London Desk</span></div></div>
    <div class="person"><div class="ph" role="img" aria-label="Portrait of a correspondent"></div><div class="name"><i></i><b>ELIN MARROW</b><span>Paris Desk</span></div></div>
    <div class="person"><div class="ph" role="img" aria-label="Portrait of a correspondent"></div><div class="name"><i></i><b>TESS ARLOW</b><span>Berlin Desk</span></div></div>
    <div class="person"><div class="ph" role="img" aria-label="Portrait of a correspondent"></div><div class="name"><i></i><b>OREN QUILL</b><span>New York Desk</span></div></div>
  </div>
  <h5>THIS WILL BE AUTOMATIC SCROLL</h5>
  <p class="note">Our correspondents report from the places where news happens. Each one brings local knowledge, trusted sources and a clear voice to the stories you read every day on our site and in our apps.</p>
</div></section>

<section class="contact">
  <div class="map" role="img" aria-label="Street map of the headquarters area">
    <div class="pin"><svg width="12" height="12" viewBox="0 0 12 12"><path d="M6 0a4 4 0 0 0-4 4c0 3 4 8 4 8s4-5 4-8a4 4 0 0 0-4-4z" fill="#fff"/></svg>HEADQUARTER</div>
  </div>
  <div class="hq">
    <h4>NEWS HEADQUARTER</h4>
    <p>1200 Harbor Lane, Suite 400<br>Portvale, NY 10099</p>
    <div class="ln"><i></i>desk@globalnewsroom.test</div>
    <div class="ln"><i></i>+1 555 014 2290</div>
    <h6>CONNECT WITH SOCIAL NETWORKS</h6>
    <div class="social"><i></i><i></i><i></i><i></i><i></i><i></i></div>
    <div class="sub-form"><span>Enter your email address</span><b>SUBMIT</b></div>
  </div>
</section>

<footer class="footer"><div class="wrap">
  <div class="fcol"><h6>News</h6><a>World News</a><a>US News</a><a>Europe</a><a>Politics</a><a>Crime</a><a>Weather</a><a>Health</a><a>Education</a><a>Science</a><a>Opinion</a><a>Columns</a><a>Obituaries</a></div>
  <div class="fcol"><h6>Sport</h6><a>Football</a><a>Tennis</a><a>Golf</a><a>Racing</a><h6 style="margin-top:10px">Business</h6><a>Markets</a><a>Economy</a><a>Companies</a><a>Property</a></div>
  <div class="fcol"><h6>Entertainment</h6><a>Film</a><a>Music</a><a>TV</a><a>Books</a><h6 style="margin-top:10px">Tech</h6><a>Gadgets</a><a>Apps</a><a>Science</a></div>
  <div class="fcol"><h6>Extra</h6><a>Newsletters</a><a>Podcasts</a><a>Video</a><a>Photos</a><a>Puzzles</a><a>Travel</a><a>Food</a><a>Style</a><a>Careers</a><a>Contact</a></div>
  <div class="fbrand"><div class="logo">LOGO</div><p>© 2014 Global News. All rights reserved. Terms of use and privacy policy apply to this site.</p></div>
</div></footer>

</body>
</html>
```